Equipment Finance Specialist I work with companies who need the funds to buy their equipment

I would like a business card that stands out on the shelves. I want to be able to hand it to someone and say WOW. This card should have my logo.
You can put color into it I am very open on design and color

What my company does is we deal with dealerships that sell equipment such as Dump Trucks garbage trucks tractors trailers. Customers get referred to us and depending on their time in business we will ask for the following items

Companies that have been in business for more than two years we have a credit application program up to 250K . With this program we need the following items Credit application filled out(which is what I would like to be able for the customer to click on my website to get.) as well as three current month bank statements.

Deals over 250k we will need the following items

2 years business tax returns
2 years personal tax returns
Profit & Loss statement
Personal Financial Statement

what we do
100% FINANCING
SEASONAL PAYMENTS
LOAN BALLOON PAYMENTS
TRAC LEASING
LOW-INTEREST REFINANCING RATES
DEBT CONSOLIDATION

We specialize in creative financing solutions and offer a variety of reliable, flexible and expandable lending choices.

Target Market(s)

Trucking Companies

Industry/Entity Type

Trucking Company

Contact Information for Business Card

* $250,000 Application only Program
* Loans from $30,000 to 5,000,000
* Competitive Interest Rates

Font styles to use
Serif
Sans Serif

Colors

Designer to choose colors to be used in the design.

Requirements
Must have
• On the back of the card.
• * $250,000 Application only Program
• * Loans from $30,000 to 5,000,000
• My name, email, website. address
• * Competitive Interest Rates
• * 100% Financing
Nice to have
• I want my logo to pop on the card
• My logo is the great one I would like to use
Should not have
• I am up for your creativity as well

```html
<!DOCTYPE html>
<html lang="en">
<head>
<meta charset="utf-8">
<title>Summit Lending – Business Card</title>
<link href="https://fonts.googleapis.com/css2?family=Source+Sans+3:wght@400;700&display=swap" rel="stylesheet">
<style>
  :root {
    --navy: #0b2a6c;
    --red: #c8102e;
    --ink: #2b2b2b;
    --grey: #5a5a5a;
    --paper: #ffffff;
    --backdrop: #e6e7ea;
  }
  * { box-sizing: border-box; margin: 0; padding: 0; }
  html, body {
    width: 1125px; height: 1200px; overflow: hidden;
    background: var(--backdrop);
    font-family: "Source Sans 3", "Helvetica Neue", Arial, sans-serif;
  }
  .canvas { position: relative; width: 1125px; height: 1200px; }
  .card {
    position: absolute; left: 162px; width: 800px; height: 457px; overflow: hidden;
  }
  .card-front { top: 95px; background: var(--paper); }
  .card-back { top: 611px; background: var(--navy); }

  .brand {
    position: absolute; top: 60px; right: 48px;
    display: flex; align-items: center; gap: 14px;
  }
  .brand-dot { width: 60px; height: 60px; border-radius: 50%; background: var(--navy); }
  .brand-name {
    font-weight: 700; font-size: 40px; line-height: 1; color: var(--navy);
    letter-spacing: 1px;
  }

  .person { position: absolute; left: 45px; top: 262px; }
  .person-name { font-weight: 700; font-size: 29px; color: var(--navy); line-height: 1.1; }
  .person-title { font-size: 22px; color: var(--red); line-height: 1.1; }

  .divider {
    position: absolute; left: 45px; right: 48px; top: 328px;
    height: 2px; background: #3a3a3a;
  }

  .contacts { position: absolute; left: 45px; top: 344px; list-style: none; }
  .contacts li {
    display: flex; align-items: center; gap: 14px;
    font-size: 20px; color: var(--grey); height: 26px;
  }
  .contacts svg { width: 19px; height: 19px; fill: var(--navy); flex: none; }

  .address {
    position: absolute; right: 48px; top: 374px; text-align: right;
    font-size: 20px; color: var(--grey); line-height: 26px; font-style: normal;
  }

  .edge-band { position: absolute; left: 0; bottom: 0; width: 800px; height: 14px; }

  .back-brand {
    position: absolute; left: 0; right: 0; top: 195px;
    display: flex; justify-content: center; align-items: center; gap: 18px;
  }
  .back-brand .brand-dot { width: 80px; height: 80px; background: var(--paper); }
  .back-brand .brand-name { color: var(--paper); font-size: 50px; }

  .offers {
    position: absolute; left: 0; right: 0; top: 381px; text-align: center;
    color: var(--paper); font-size: 20px; line-height: 26px;
  }
</style>
</head>
<body>
<main class="canvas">

  <section class="card card-front" aria-label="Business card front">
    <div class="brand">
      <span class="brand-dot"></span>
      <span class="brand-name">SUMMIT LENDING</span>
    </div>

    <div class="person">
      <p class="person-name">MARK ELLISON</p>
      <p class="person-title">PRESIDENT</p>
    </div>

    <div class="divider"></div>

    <ul class="contacts">
      <li>
        <svg viewBox="0 0 20 20" aria-hidden="true"><path d="M2 7c0-3 4-4 8-4s8 1 8 4v1h-4V6.5c-1-.5-2.5-.7-4-.7s-3 .2-4 .7V8H2zM5 9h10l2 8H3z"/></svg>
        555 0142 3318
      </li>
      <li>
        <svg viewBox="0 0 20 20" aria-hidden="true"><path d="M1 4h18v2l-9 5-9-5zM1 8l9 5 9-5v8H1z"/></svg>
        mark@summitlending.com
      </li>
      <li>
        <svg viewBox="0 0 20 20" aria-hidden="true"><circle cx="10" cy="10" r="9"/><path d="M6 5c2 1 3 3 2 5s1 3 0 5M13 4c-1 2 1 3 2 4" stroke="#fff" stroke-width="1.5" fill="none"/></svg>
        www.summitlending.com
      </li>
    </ul>

    <address class="address">
      2719 Harbor Lane<br>
      Maple Grove, NY 10000
    </address>

    <svg class="edge-band" viewBox="0 0 800 14" preserveAspectRatio="none" aria-hidden="true">
      <polygon points="0,2 450,2 446,14 0,14" fill="var(--navy)"/>
      <polygon points="455,0 800,0 800,14 451,14" fill="var(--red)"/>
    </svg>
  </section>

  <section class="card card-back" aria-label="Business card back">
    <div class="back-brand">
      <span class="brand-dot"></span>
      <span class="brand-name">SUMMIT LENDING</span>
    </div>

    <div class="offers">
      <p>$250,000 Application only Program ● Loans from $30,000 to 5,000,000</p>
      <p>Competitive Interest Rates ● 100% Financing</p>
    </div>
  </section>

</main>
</body>
</html>
```